Salon and Spa Distributor Business Card

Need a business card. We are are distributor in the salon and spa industry. We identify with natural beauty. Need a card with:
Company Name: Petal Quarry"
Title: "President & CEO"
Address
Company Phone number
email
website
Tag Line:" The Professional Salon Source"

Industry/Entity Type

Business

Contact Information for Business Card

Name: Dov Strommen
Title: "President & CEO"
Address: 31 Harlow Ln, Bexmoor, NJ 07813
Company Phone number: 800-463-5918
email: dovstrommen@petalquarry.example
website: www.petalquarry.example

Requirements
Should not have
• No black backgrounds

```html
<!DOCTYPE html>
<html lang="en">
<head>
<meta charset="utf-8">
<title>Petal Quarry — Business Card</title>
<link rel="stylesheet" href="https://fonts.googleapis.com/css2?family=Dosis:wght@400;500&display=swap">
<style>
  :root {
    --leaf-light: #7cc242;
    --leaf-mid: #4fa83a;
    --leaf-dark: #2b8a3a;
    --ink-green: #3f9b3b;
    --paper: #ffffff;
  }
  html, body {
    margin: 0;
    padding: 0;
    overflow: hidden;
    background: var(--paper);
  }
  .card {
    position: relative;
    width: 1200px;
    height: 720px;
    overflow: hidden;
    background: var(--paper);
    font-family: "Dosis", "Trebuchet MS", sans-serif;
  }
  .card__swooshes {
    position: absolute;
    inset: 0;
    width: 1200px;
    height: 720px;
  }
  .brand {
    position: absolute;
    left: 704px;
    top: 40px;
    transform: translateX(-50%);
    text-align: center;
    color: var(--ink-green);
    white-space: nowrap;
  }
  .brand__name {
    margin: 0;
    font-size: 64px;
    font-weight: 400;
    line-height: 1.05;
  }
  .brand__tagline {
    margin: 0;
    font-size: 37px;
    font-weight: 400;
    line-height: 1.1;
  }
  .person {
    position: absolute;
    left: 704px;
    top: 258px;
    transform: translateX(-50%);
    text-align: center;
    color: var(--leaf-dark);
    white-space: nowrap;
  }
  .person__name {
    margin: 0;
    font-size: 88px;
    font-weight: 400;
    line-height: 1;
  }
  .person__title {
    margin: 6px 0 0;
    font-size: 46px;
    font-weight: 400;
    line-height: 1.1;
  }
  .contact {
    position: absolute;
    right: 45px;
    top: 610px;
    text-align: right;
    color: var(--paper);
    font-size: 30px;
    line-height: 46px;
    white-space: nowrap;
  }
  .contact__line { margin: 0; }
  .contact__sep { margin: 0 12px; }
</style>
</head>
<body>
  <div class="card">
    <svg class="card__swooshes" viewBox="0 0 1200 720" aria-hidden="false">
      <defs>
        <linearGradient id="leafSprigTone" x1="0" y1="0" x2="1" y2="1">
          <stop offset="0" stop-color="#8fd05a"/>
          <stop offset="1" stop-color="#5cb343"/>
        </linearGradient>
      </defs>
      <!-- top-right corner sweep -->
      <path d="M 900 0 L 1200 0 L 1200 440 C 1180 250 1080 90 900 0 Z" fill="var(--leaf-light)"/>
      <path d="M 1040 0 C 1170 80 1210 230 1190 430 C 1215 250 1200 90 1120 0 Z" fill="var(--leaf-mid)"/>
      <!-- thin dark arc under the name -->
      <path d="M 150 300 C 350 520 850 520 1200 340 L 1200 352 C 850 540 340 540 150 300 Z" fill="var(--leaf-dark)"/>
      <!-- light band -->
      <path d="M 0 410 C 350 580 820 500 1200 360 L 1200 720 L 0 720 Z" fill="var(--leaf-light)"/>
      <!-- dark base -->
      <path d="M 0 455 C 360 630 820 560 1200 420 L 1200 720 L 0 720 Z" fill="var(--leaf-dark)"/>
      <!-- brand mark placeholder -->
      <circle class="brand-mark" cx="240" cy="140" r="92" fill="var(--leaf-mid)"/>
      <!-- leaf sprig decoration area -->
      <rect class="leaf-sprigs" x="10" y="470" width="250" height="230" rx="110"
            fill="url(#leafSprigTone)" opacity="0.85"
            role="img" aria-label="Decorative green leaf sprigs"/>
    </svg>

    <header class="brand">
      <h1 class="brand__name">PetalQuarry</h1>
      <p class="brand__tagline">The Professional Salon Source</p>
    </header>

    <section class="person">
      <h2 class="person__name">Dov Strommen</h2>
      <p class="person__title">President &amp; CEO</p>
    </section>

    <address class="contact" style="font-style: normal;">
      <p class="contact__line">31 Harlow Ln, Bexmoor, NJ 07813<span class="contact__sep">·</span>800-463-5918</p>
      <p class="contact__line">dovstrommen@petalquarry.example<span class="contact__sep">·</span>www.petalquarry.example</p>
    </address>
  </div>
</body>
</html>
```